Harbor Light Church San Francisco needs a Leadership Booklet designed.

We need a Leadership Booklet to be designed and formatted. The content is currently 27 pages and involves headings, quotes, bolded statements and scripture that we would like to stick out. We also need a cover designed for it as well. Cover - "Harbor Light Leadership Development"

Here is a link to our Harbor Light Church style guide.
https://studio-38261.brandvault.example/d/7QwRkPzN2bYc/harbor-light-church-style-guide

Target Market(s)

Leaders within our church.

Font styles to use
Sans Serif

```html
<!DOCTYPE html>
<html lang="en">
<head>
<meta charset="utf-8">
<title>Harbor Light Leadership Development – Booklet Spread</title>
<link href="https://fonts.googleapis.com/css2?family=Mulish:wght@300;400;700;800&family=Jost:wght@500;600&display=swap" rel="stylesheet">
<style>
  :root {
    --backdrop: #e7e8e9;
    --paper: #ffffff;
    --ink: #1d1d1b;
    --ink-soft: #3a3a3a;
    --rule: #4a4a4a;
    --brand-green: #6ab545;
    --shadow: rgba(0, 0, 0, 0.28);
  }
  * { margin: 0; padding: 0; box-sizing: border-box; }
  html, body {
    width: 1200px; height: 837px; overflow: hidden;
    background: var(--backdrop);
    font-family: "Mulish", "Helvetica Neue", Arial, sans-serif;
    color: var(--ink);
  }
  .spread { position: relative; width: 1200px; height: 837px; }
  .page-label {
    position: absolute; top: 22px; width: 120px; text-align: center;
    font-size: 21px; font-weight: 400; color: var(--ink);
  }
  .page-label--left { left: 278px; }
  .page-label--right { left: 809px; }

  .page {
    position: absolute; top: 60px; width: 506px; height: 716px;
    background: var(--paper);
    box-shadow: 5px 5px 6px var(--shadow);
    overflow: hidden;
  }
  .page--left { left: 76px; }
  .page--right { left: 617px; }

  .page-body {
    position: absolute; left: 59px; width: 392px;
    font-size: 9.3px; line-height: 13.4px; font-weight: 300;
    text-align: justify; color: var(--ink-soft);
  }
  .page--left .page-body { top: 72px; }
  .page--right .page-body { top: 110px; }
  .page-body p { margin-bottom: 13.4px; }
  .page-body .scripture,
  .page-body .emphasis { font-weight: 700; color: var(--ink); }
  .page-body .lead { margin-bottom: 13.4px; }
  .page-body .lead strong { font-weight: 800; color: var(--ink); }
  .page-body .ragged { text-align: left; }

  .section-title {
    position: absolute; top: 40px; left: 110px; width: 286px; height: 43px;
    border-radius: 22px; background: var(--brand-green);
    color: #fff; font-family: "Jost", "Futura", sans-serif; font-weight: 500;
    font-size: 22px; line-height: 43px; text-align: center; letter-spacing: 0.1px;
  }

  .page-footer { position: absolute; left: 0; top: 664px; width: 506px; height: 32px; }
  .footer-rules { position: absolute; left: 0; top: 0; }
  .footer-mark {
    position: absolute; left: 394px; top: 6px; width: 108px;
    display: flex; align-items: center; gap: 4px;
  }
  .footer-mark__square { width: 8px; height: 8px; background: var(--brand-green); flex: none; }
  .footer-mark__name {
    font-size: 9px; line-height: 10px; font-weight: 400; color: var(--brand-green);
  }
</style>
</head>
<body>
<main class="spread">
  <div class="page-label page-label--left">pg-2</div>
  <div class="page-label page-label--right">pg-3</div>

  <section class="page page--left">
    <div class="page-body">
      <p class="scripture">3 Now Moses was tending the flock of Jethro his father-in-law, the priest of Midian, and he led the flock to the far side of the wilderness and came to Horeb,the mountain of God. 2 There the angel of the Lord appeared to him in flames of fire from within a bush. Moses saw that though the bush was on fire it did not burn up. 3 So Moses thought, “I will go over and see this strange sight— why the bush does not burn up.”</p>
      <p class="scripture">4 When the Lord saw that he had gone over to look, God called to him from within the bush, “Moses! Moses!”</p>
      <p class="scripture">And Moses said, “Here I am.”</p>
      <p class="scripture">5 “Do not come any closer,” God said. “Take off your sandals, for the place where you are standing is holy ground.” 6 Then he said, “I am the God of your father,[a] the God of Abraham, the God of Isaac and the God of Jacob.” At this, Moses hid his face, because he was afraid to look at God.</p>
      <p class="scripture">7 The Lord said, “I have indeed seen the misery of my people in Egypt. I have heard them crying out because of their slave drivers, and I am concerned about their suffering. 8 So I have come down to rescue them from the hand of the Egyptians and to bring them up out of that land into a good and spacious land, a land flowing with milk and honey—the home of the Canaanites, Hittites, Amorites, Perizzites, Hivites and Jebusites. 9 And now the cry of the Israelites has reached me, and I have seen the way the Egyptians are oppressing them. 10 So now, go. I am sending you to Pharaoh to bring my people the Israelites out of Egypt.”</p>
      <p>Notice how this begins. We are simply told about all that God is doing. God heard. God remembered. God looked. God was concerned. So far, the only one playing a part is God.</p>
      <p>Then comes the infamous burning bush experience. Moses was tending the flock of Jethro, his father-in-law. God gets his attention. Then God lets him know what He has seen and how He is concerned. God says, “I have come down to rescue them.” This had to make Moses excited, but he must have wondered, “Why is God telling all of this to me?”</p>
      <p class="ragged">In verse 10, we learn why God is telling this to Moses. “So now, go. I am sending you to bring my people the Israelites out of Egypt.”</p>
      <p class="emphasis">Perhaps, part of the reason God has sent you to San Francisco at this time is because he wants you to play a part in helping us accomplish the vision He has given Harbor Light Church.</p>
      <p class="ragged">Can you see what God is doing in Harbor Light and in San Francisco? How might He be calling you to be a part of it?</p>
    </div>
    <footer class="page-footer">
      <svg class="footer-rules" width="390" height="28" viewBox="0 0 390 28" aria-hidden="true">
        <rect x="0" y="0" width="385" height="4" fill="var(--rule)"/>
        <rect x="0" y="11" width="385" height="4" fill="var(--rule)"/>
        <rect x="0" y="22" width="385" height="4" fill="var(--rule)"/>
      </svg>
      <div class="footer-mark">
        <span class="footer-mark__square"></span>
        <span class="footer-mark__name">Harbor Light Church San Francisco</span>
      </div>
    </footer>
  </section>

  <section class="page page--right">
    <h1 class="section-title">Who Harbor Light Leaders Are</h1>
    <div class="page-body">
      <div class="lead">As Christian leaders, never forget this:<br><strong>WE ARE FOLLOWERS BEFORE WE ARE LEADERS.</strong></div>
      <p>Before we lead others, let’s make sure we are orienting our entire lives around Jesus. We can’t give others what we lack ourselves. Never forget what Jesus said in John 15:5, “I am the vine; you are the branches. If you remain in me and I in you, you will bear much fruit; apart from me you can do nothing.”</p>
      <p>One of the greatest leadership lessons we can learn from watching other leaders throughout the world is this:</p>
      <p class="emphasis">It is dangerous to have an outer life that your inner life cannot keep up with.</p>
      <p>“One of the great and subtle temptations of leadership is to neglect the inner life and your relationship with God because of the many things which demand immediate attention.” - Samuel Crane, The Call to Lead</p>
      <p>“Because my inner life is invisible, it is easy to neglect.” - James Oakley, Inner Keeping</p>
      <p>“The most important thing in your life is not what you do; it’s who you become.” - Daniel Whitford</p>
      <p class="scripture">Philippians 1:6 being confident of this, that he who began a good work in you will carry it on to completion until the day of Christ Jesus.</p>
      <p class="scripture ragged">Galatians 4:19 My dear children, for whom I am again in the pains of childbirth<br>until Christ is FORMED in you</p>
      <p>Christian leadership certainly has a lot to do with the work that we do for God and we’ll get there in the next section. We’re mostly interested in what we can produce in this world, but God is mostly interested in what He can produce in us. Here’s a question we should ask:</p>
      <p class="emphasis">How can I position myself so that God can do His work in me?</p>
      <p class="scripture">Luke 6:43-45 “No good tree bears bad fruit, nor does a bad tree bear good fruit. 44 Each tree is recognized by its own fruit. People do not pick figs from thornbushes, or grapes from briers. 45 A good man brings good things out of the good stored up in his heart, and an evil man brings evil things out of the evil stored up in his heart. For the mouth speaks what the heart is full of.</p>
    </div>
    <footer class="page-footer">
      <svg class="footer-rules" width="390" height="28" viewBox="0 0 390 28" aria-hidden="true">
        <rect x="0" y="0" width="385" height="4" fill="var(--rule)"/>
        <rect x="0" y="11" width="385" height="4" fill="var(--rule)"/>
        <rect x="0" y="22" width="385" height="4" fill="var(--rule)"/>
      </svg>
      <div class="footer-mark">
        <span class="footer-mark__square"></span>
        <span class="footer-mark__name">Harbor Light Church San Francisco</span>
      </div>
    </footer>
  </section>
</main>
</body>
</html>
```